website design for M&T Electric

A portfolio website for a high end commercial and residential electrical contracting company. The current site mandtelectric.example does not represent the current direction but the images in the gallery give you an idea of the work we do. Current logo will be uploaded shortly but is black text on white background.
Target Market(s)
General Contractors, Residential Home Owners, clients intersted in Velmora home automation.
Industry/Entity Type
Electrician
Coding
Coded - Design and coding required
Number of Pages Required
2 page
Font styles to use
Sans Serif
Colors
Designer to choose colors to be used in the design.
Requirements
Must have
- Portfolio section highlighting different service areas and products (Velmora Housepilot, etc)

```html
<!DOCTYPE html>
<html lang="en">
<head>
<meta charset="utf-8">
<title>M&amp;T Electric</title>
<link href="https://fonts.googleapis.com/css2?family=Nunito+Sans:wght@400;600;700&display=swap" rel="stylesheet">
<style>
:root{
  --orange:#f7931e;
  --orange-deep:#e8820c;
  --green:#5cc71f;
  --ink:#2b2b2b;
  --muted:#8a8a8a;
  --grey-band:#e8e8e8;
  --footer:#e6e6e6;
  --white:#ffffff;
  --hero-a:#0f1a5c;
  --hero-b:#2a3f9e;
  --hero-c:#5a3a2a;
}
*{margin:0;padding:0;box-sizing:border-box}
html,body{width:1200px;height:2586px;overflow:hidden}
body{font-family:"Nunito Sans",sans-serif;color:var(--ink);background:var(--white);position:relative}
.abs{position:absolute}

/* Hero */
.hero{left:0;top:0;width:1200px;height:690px;
  background:radial-gradient(ellipse at 60% 45%,var(--hero-b) 0%,var(--hero-a) 60%,#070c30 100%);}
.hero-glow{left:0;top:0;width:1200px;height:690px;
  background:radial-gradient(ellipse at 25% 30%,rgba(150,90,50,.55),transparent 45%),
             radial-gradient(ellipse at 85% 65%,rgba(90,110,200,.35),transparent 40%)}
.hero-curve{left:0;top:600px;width:1200px;height:92px}
.logo{left:117px;top:38px;color:var(--white);font-size:38px;font-weight:400;letter-spacing:.5px}
.nav{top:48px;left:0;width:1200px}
.nav a{position:absolute;color:var(--white);text-decoration:none;font-size:18px;font-weight:700}
.search{left:1044px;top:50px}
.hero-title{top:274px;width:1200px;text-align:center;color:var(--white);font-size:43px;font-weight:700;letter-spacing:.3px}
.hero-sub{top:328px;width:1200px;text-align:center;color:var(--orange);font-size:28px;font-weight:600}
.btn{display:block;text-align:center;background:var(--orange);color:var(--white);font-weight:700;border-radius:21px;text-decoration:none;text-transform:uppercase}
.hero-btn{left:527px;top:382px;width:146px;height:42px;line-height:42px;font-size:15px}
.dots{top:602px;left:553px}
.dots span{display:inline-block;width:15px;height:15px;border-radius:50%;background:var(--white);margin-right:7px}
.dots span.hollow{background:transparent;border:2px solid var(--white)}

/* Service row */
.service{top:715px;width:320px;height:150px}
.service-icon{left:0;top:0;width:100px;height:100px;border-radius:50%;border:2px solid #d9d9d9;background:var(--white)}
.service h3{left:114px;top:0;font-size:24px;font-weight:400;line-height:27px}
.service p{left:114px;top:62px;width:185px;font-size:13px;color:var(--muted);line-height:18px}
.service .more{left:114px;top:125px;font-size:15px;color:var(--orange);font-weight:600}

/* Speciality */
.speciality{left:0;top:919px;width:1200px;height:589px;
  background:linear-gradient(to bottom,var(--grey-band) 0%,var(--grey-band) 70%,var(--white) 70%)}
.eyebrow{top:955px;width:1200px;text-align:center;color:var(--orange);font-size:19px}
.section-title{top:981px;width:1200px;text-align:center;font-size:28px;font-weight:600;color:#333}
.intro{top:1030px;left:195px;width:810px;text-align:center;color:var(--muted);font-size:15px;line-height:25px}
.card{top:1117px;width:308px;height:343px;background:var(--white);border:1px solid #d0d0d0;box-shadow:0 1px 3px rgba(0,0,0,.12)}
.card-photo{left:0;top:0;width:306px;height:185px}
.card h4{top:205px;width:306px;text-align:center;font-size:22px;font-weight:400}
.card p{top:242px;left:28px;width:250px;text-align:center;font-size:13px;color:var(--muted);line-height:20px}
.card .btn{left:86px;top:322px;width:134px;height:40px;line-height:40px;font-size:14px}

/* About */
.about-left{left:0;top:1557px;width:600px;height:477px;background:linear-gradient(135deg,#e8871e,var(--orange-deep) 55%,#c86a10)}
.about-right{left:600px;top:1557px;width:600px;height:477px;background:linear-gradient(160deg,#9aa4c8 0%,#5c5e6e 45%,#5a3b26 100%)}
.about h2{left:115px;top:1650px;color:var(--white);font-size:34px;font-weight:400}
.about p{left:115px;width:470px;color:var(--white);font-size:15px;line-height:20px}
.about .outline{left:114px;top:1887px;width:137px;height:40px;line-height:36px;border:2px solid var(--white);border-radius:20px;text-align:center;color:var(--white);font-size:14px;font-weight:700}

/* Recent work */
.recent-title{left:124px;top:2080px;font-size:32px;font-weight:400}
.work{top:2138px;width:219px;height:236px;background:var(--white);border:4px solid var(--white);box-shadow:0 0 10px rgba(0,0,0,.15)}
.work-photo{left:0;top:0;width:211px;height:172px}
.work-bar{left:0;top:172px;width:211px;height:56px;background:var(--green);color:var(--white);padding:8px 0 0 14px}
.work-bar strong{display:block;font-size:19px;font-weight:600;line-height:22px}
.work-bar small{font-size:11px}

/* Footer */
.footer{left:0;top:2445px;width:1200px;height:141px;background:var(--footer)}
.footer-nav{top:2487px;left:126px}
.footer-nav a{color:var(--ink);text-decoration:none;font-size:17px;margin-right:24px}
.copyright{top:2523px;left:126px;font-size:12px}
.social{top:2493px;left:924px}
.social span{display:inline-block;width:31px;height:31px;border:2px solid #222;border-radius:50%;margin-right:4px}
</style>
</head>
<body>

<header>
  <div class="abs hero" role="img" aria-label="Close-up photo of glowing LED light strips"></div>
  <div class="abs hero-glow"></div>
  <svg class="abs hero-curve" viewBox="0 0 1200 92" preserveAspectRatio="none" aria-hidden="true">
    <path d="M0 92 L0 92 Q700 -30 1200 92 Z" fill="#ffffff"/>
  </svg>
  <div class="abs logo">M&amp;T Electric</div>
  <nav class="abs nav">
    <a style="left:495px" href="#">Home</a>
    <a style="left:579px" href="#">Gallery</a>
    <a style="left:672px" href="#">Speciality Services</a>
    <a style="left:862px" href="#">About</a>
    <a style="left:948px" href="#">Contact</a>
  </nav>
  <svg class="abs search" width="20" height="20" viewBox="0 0 20 20" aria-label="Search">
    <circle cx="8" cy="8" r="6" fill="none" stroke="#fff" stroke-width="3"/>
    <line x1="12.5" y1="12.5" x2="18" y2="18" stroke="#fff" stroke-width="3" stroke-linecap="round"/>
  </svg>
  <h1 class="abs hero-title">COMMECIAL ELECTRICAL SERVICE</h1>
  <div class="abs hero-sub">CURABITUR VEL MISIT AMET MALESUAD</div>
  <a class="abs btn hero-btn" href="#">Read More</a>
  <div class="abs dots"><span class="hollow"></span><span></span><span></span><span></span></div>
</header>

<section>
  <div class="abs service" style="left:115px">
    <svg class="abs service-icon" viewBox="0 0 100 100" aria-label="Lamp icon">
      <path d="M36 30 H64 L70 52 H30 Z" fill="#f7931e"/>
      <rect x="48" y="52" width="4" height="22" fill="#f7931e"/>
      <path d="M38 78 Q50 70 62 78 Z" fill="#f7931e"/>
    </svg>
    <h3 class="abs">Residential<br>Services</h3>
    <p class="abs">Morbi diam mauris viverra in gravida eu mattis in ante Morbi eget arcu Morbi porta</p>
    <div class="abs more">Click here ›</div>
  </div>
  <div class="abs service" style="left:440px">
    <svg class="abs service-icon" viewBox="0 0 100 100" aria-label="Bulb icon">
      <g transform="rotate(40 50 50)" fill="none" stroke="#f7931e" stroke-width="3">
        <path d="M50 22 C64 30 64 58 56 66 H44 C36 58 36 30 50 22 Z"/>
        <rect x="44" y="66" width="12" height="10"/>
      </g>
    </svg>
    <h3 class="abs">Commecial<br>Services</h3>
    <p class="abs">Morbi diam mauris viverra in gravida eu mattis in ante Morbi eget arcu Morbi porta</p>
    <div class="abs more">Click here ›</div>
  </div>
  <div class="abs service" style="left:772px">
    <svg class="abs service-icon" viewBox="0 0 100 100" aria-label="House icon">
      <path d="M50 24 L74 38 V66 L50 80 L26 66 V38 Z" fill="none" stroke="#f7931e" stroke-width="3"/>
      <path d="M38 60 V46 L50 38 L62 46 V60 Z" fill="none" stroke="#f7931e" stroke-width="3"/>
    </svg>
    <h3 class="abs">Landscape<br>Services</h3>
    <p class="abs">Morbi diam mauris viverra in gravida eu mattis in ante Morbi eget arcu Morbi porta</p>
    <div class="abs more">Click here ›</div>
  </div>
</section>

<section>
  <div class="abs speciality"></div>
  <div class="abs eyebrow">WHAT WE DO</div>
  <h2 class="abs section-title">SPECIALITY SERVICES</h2>
  <p class="abs intro">Allamcorper est eget tempor cursus neque mi consectetuer mi a ultricies massa est sed nisl Class aptent taciti sociosqu ad litora torquent per conubia nostra per inceptos hymenaeos Proin nulla arcu</p>

  <article class="abs card" style="left:115px">
    <div class="abs card-photo" role="img" aria-label="Photo of a wall-mounted lighting control keypad" style="background:linear-gradient(135deg,#d9b27a,#8a6a48)"></div>
    <h4 class="abs">Velmora Housepilot</h4>
    <p class="abs">Morbi diam mauris viverra in gravida eu mattis in ante Morbi eget arcu Morbi porta libero id ullamcorper</p>
    <a class="abs btn" href="#">Read More</a>
  </article>
  <article class="abs card" style="left:441px">
    <div class="abs card-photo" role="img" aria-label="Photo of glowing hanging LED bulbs" style="background:radial-gradient(ellipse at 50% 60%,#ffd99a,#b06a18 50%,#3a1e08)"></div>
    <h4 class="abs">LED Lighting</h4>
    <p class="abs">Morbi diam mauris viverra in gravida eu mattis in ante Morbi eget arcu Morbi porta ullamcorper</p>
    <a class="abs btn" href="#">Read More</a>
  </article>
  <article class="abs card" style="left:771px">
    <div class="abs card-photo" role="img" aria-label="Photo of a standby generator beside a house" style="background:linear-gradient(160deg,#9aa6b4,#c9c9c4 50%,#8a6a5a)"></div>
    <h4 class="abs">Emergency Generators</h4>
    <p class="abs">Morbi diam mauris viverra in gravida eu mattis in ante Morbi eget arcu Morbi porta ullamcorper</p>
    <a class="abs btn" href="#">Read More</a>
  </article>
</section>

<section class="about">
  <div class="abs about-left" role="img" aria-label="Photo of a bright interior under an orange tint"></div>
  <div class="abs about-right" role="img" aria-label="Photo of a modern living room with cove lighting"></div>
  <h2 class="abs">About M&amp;T Electric</h2>
  <p class="abs" style="top:1704px">Praesent elementum elit at tellus nec ultricies sit amet porttitor mattis enim in massa libero interdum nec interdum vel blandit sed nulla in ullamcorper est</p>
  <p class="abs" style="top:1780px">eget tempor cursus neque mi consectetuer mi a ultricies massa est sed nisl Class aptent taciti sociosqu ad litora torquent per conubia nostra per inceptos hymenaeos Proin nulla arcu nonummy luctus dictum eget fermentum et lorem</p>
  <a class="abs outline" href="#">READ MORE</a>
</section>

<section>
  <h2 class="abs recent-title">Recent Work</h2>
  <article class="abs work" style="left:117px">
    <div class="abs work-photo" role="img" aria-label="Photo of a lit commercial lobby" style="background:linear-gradient(160deg,#e6e0d2,#a89e88)"></div>
    <div class="abs work-bar"><strong>Project Tittle</strong><small>Donec dictum lectus non odio →</small></div>
  </article>
  <article class="abs work" style="left:364px">
    <div class="abs work-photo" role="img" aria-label="Photo of an industrial steel roof structure" style="background:linear-gradient(160deg,#d2d6dc,#5e6670)"></div>
    <div class="abs work-bar"><strong>Project Tittle</strong><small>Donec dictum lectus non odio →</small></div>
  </article>
  <article class="abs work" style="left:609px">
    <div class="abs work-photo" role="img" aria-label="Photo of a warmly lit dining room" style="background:linear-gradient(160deg,#7a6ab0,#c9845a 60%,#6a3a20)"></div>
    <div class="abs work-bar"><strong>Project Tittle</strong><small>Donec dictum lectus non odio →</small></div>
  </article>
  <article class="abs work" style="left:857px">
    <div class="abs work-photo" role="img" aria-label="Photo of an electrician installing a wall light" style="background:linear-gradient(160deg,#efd6c4,#b07a5a)"></div>
    <div class="abs work-bar"><strong>Project Tittle</strong><small>Donec dictum lectus non odio →</small></div>
  </article>
</section>

<footer>
  <div class="abs footer"></div>
  <nav class="abs footer-nav">
    <a href="#">Home</a><a href="#">Gallery</a><a href="#">Speciality Services</a><a href="#">About</a><a href="#">Contact</a>
  </nav>
  <div class="abs copyright">© 2017 Company Name &nbsp;All right reserved &nbsp;Term of Use</div>
  <div class="abs social" aria-label="Social links"><span></span><span></span><span></span><span></span></div>
</footer>

</body>
</html>
```